Dietitian needs awesome business card

I need a contemporary design that's eye catching but professional.
My card is to given to doctors, specialists and patients alike.
I manage patients with chronic diseases
I have uploaded my logo and current business card, I would also like the other Certified Clinical Nutritionist logo incorporated into the design

Target Market(s)

Doctors, specialists and patients

Industry/Entity Type

Healthcare

Contact Information for Business Card

www.brightfieldnutrition.com.au
Ph: 0427 561 903
Fax: 6457 2183
email: marcus.k.diet@fernmail.com
Space on the back of the card with: Appointment date, Appointment time and appointment location

Font styles to use
Serif

Colors
fbee3e
876aae
ffc214

Requirements
Must have
• My Logo
• Certified Clinical Nutritionist Logo
• My 4 locations - Pinebrook Medical Centre, North Corrin Health, Hollis Medical, Ashcombe Doctors Surgery
Nice to have
• I like the colours in my current business card

```html
<!DOCTYPE html>
<html lang="en">
<head>
<meta charset="utf-8">
<title>Brightfield Nutrition &amp; Dietetics – Business Card</title>
<link rel="stylesheet" href="https://fonts.googleapis.com/css2?family=Gelasio:ital,wght@0,400;0,600;1,400&display=swap">
<style>
  :root {
    --bg: #e9e6e1;
    --card: #ffffff;
    --blue: #1f4c9e;
    --blue-deep: #16367a;
    --green: #8cc63f;
    --orange: #f47b20;
    --ink: #2b2b2b;
    --rule: #b9bcc4;
    --dot: #4a6fb5;
  }
  * { box-sizing: border-box; margin: 0; padding: 0; }
  html, body { width: 1200px; height: 843px; overflow: hidden; }
  body {
    background: var(--bg);
    font-family: "Gelasio", Georgia, serif;
    color: var(--ink);
    position: relative;
  }
  .card {
    position: absolute;
    left: 280px;
    width: 640px;
    height: 366px;
    background: var(--card);
    box-shadow: 0 6px 18px rgba(0,0,0,.18);
    overflow: hidden;
  }
  .card--back { top: 36px; }
  .card--front { top: 442px; }

  /* Back */
  .brand-dot {
    position: absolute;
    border-radius: 50%;
    background: linear-gradient(135deg, var(--blue) 0 50%, var(--green) 50% 100%);
  }
  .card--back .brand-dot { left: 40px; top: 56px; width: 44px; height: 44px; }
  .badge {
    position: absolute; right: 40px; top: 26px;
    width: 150px; height: 46px;
    background: var(--orange);
    display: flex; align-items: center; gap: 8px; padding: 0 10px;
  }
  .badge__text { color: #fff; font-size: 9.5px; line-height: 1.15; flex: 1; }
  .badge__seal { width: 40px; height: 30px; border-radius: 4px; background: #fff; }
  .write-line { position: absolute; left: 104px; right: 40px; height: 1px; background: var(--rule); }
  .field {
    position: absolute; color: var(--blue); font-size: 15px;
    display: flex; align-items: flex-end; gap: 6px;
  }
  .field__dots { flex: 1; border-bottom: 2px dotted var(--dot); height: 1px; margin-bottom: 4px; }
  .field__suffix { font-size: 11px; }
  .locations {
    position: absolute; left: 40px; right: 40px; top: 282px;
    display: grid; grid-template-columns: 1fr 1fr; row-gap: 8px; column-gap: 20px;
    list-style: none; font-size: 14px; color: var(--ink);
  }
  .locations li { display: flex; align-items: center; gap: 8px; }
  .locations li::before {
    content: ""; width: 11px; height: 11px; border: 1.5px solid var(--blue);
  }

  /* Front */
  .logo-block {
    position: absolute; left: 40px; top: 124px; width: 256px;
    display: flex; align-items: center; gap: 12px;
  }
  .card--front .brand-dot { position: static; width: 52px; height: 52px; flex: none; }
  .logo-block__name {
    color: var(--blue); font-size: 18px; line-height: 1.2; font-weight: 400;
    white-space: nowrap;
  }
  .divider { position: absolute; left: 316px; top: 96px; width: 1px; height: 120px; background: #cfd2d8; }
  .person { position: absolute; left: 340px; top: 100px; }
  .person__name { color: var(--blue); font-size: 25px; font-weight: 600; letter-spacing: .3px; }
  .person__role { color: var(--green); font-size: 16px; margin-top: 2px; }
  .contacts { list-style: none; margin-top: 10px; font-size: 15.5px; }
  .contacts li { display: flex; align-items: center; gap: 10px; height: 24px; }
  .contacts svg { width: 15px; height: 15px; fill: var(--blue); flex: none; }
  .band { position: absolute; left: 0; bottom: 0; width: 640px; height: 100px; }
  .website {
    position: absolute; left: 0; right: 0; bottom: 16px;
    text-align: center; color: #fff; font-style: italic; font-size: 17px; letter-spacing: .4px;
  }
</style>
</head>
<body>

  <section class="card card--back" aria-label="Card back – appointment">
    <span class="brand-dot"></span>
    <div class="badge">
      <span class="badge__text">Certified Clinical Nutritionist</span>
      <span class="badge__seal"></span>
    </div>
    <span class="write-line" style="top:112px"></span>
    <span class="write-line" style="top:150px"></span>
    <span class="write-line" style="top:188px; left:40px"></span>
    <div class="field" style="left:320px; right:40px; top:124px;">
      <span>Time :</span><span class="field__dots"></span><span class="field__suffix">AM/PM</span>
    </div>
    <div class="field" style="left:40px; right:40px; top:226px;">
      <span>Date :</span><span class="field__dots"></span>
    </div>
    <ul class="locations">
      <li>Pinebrook Medical Centre</li>
      <li>Ashcombe Doctors Surgery</li>
      <li>North Corrin Health</li>
      <li>Hollis Medical</li>
    </ul>
  </section>

  <section class="card card--front" aria-label="Card front – contact">
    <div class="logo-block">
      <span class="brand-dot"></span>
      <span class="logo-block__name">Brightfield<br>Nutrition &amp; Dietetics</span>
    </div>
    <span class="divider"></span>
    <div class="person">
      <h1 class="person__name">Marcus Kellaway</h1>
      <p class="person__role">Nutritionist &amp; Chef</p>
      <ul class="contacts">
        <li><svg viewBox="0 0 24 24"><path d="M6.6 10.8a15.1 15.1 0 0 0 6.6 6.6l2.2-2.2c.3-.3.7-.4 1-.2 1.1.4 2.3.6 3.6.6.6 0 1 .4 1 1V20c0 .6-.4 1-1 1A17 17 0 0 1 3 4c0-.6.4-1 1-1h3.5c.6 0 1 .4 1 1 0 1.3.2 2.5.6 3.6.1.3 0 .7-.2 1z"/></svg>0427 561 903</li>
        <li><svg viewBox="0 0 24 24"><path d="M7 2h8l2 2v4H7zM4 9h16a2 2 0 0 1 2 2v7h-4v4H6v-4H2v-7a2 2 0 0 1 2-2zm4 8v3h8v-3z"/></svg>6457 2183</li>
        <li><svg viewBox="0 0 24 24"><path d="M2 5h20v14H2zm2 2v.5l8 5 8-5V7z"/></svg>marcus.k.diet@fernmail.com</li>
      </ul>
    </div>
    <svg class="band" viewBox="0 0 640 100" preserveAspectRatio="none" aria-hidden="true">
      <defs>
        <linearGradient id="bandFill" x1="0" y1="0" x2="1" y2="0">
          <stop offset="0" stop-color="#2a63c0"/>
          <stop offset="1" stop-color="#16367a"/>
        </linearGradient>
      </defs>
      <path d="M0 8 C200 46 420 50 640 40 L640 100 L0 100 Z" fill="#8cc63f"/>
      <path d="M0 16 C200 54 420 58 640 48 L640 100 L0 100 Z" fill="url(#bandFill)"/>
    </svg>
    <p class="website">www.brightfieldnutrition.com.au</p>
  </section>

</body>
</html>
```